Young, dynamic furniture company needs a new business card design

We require a new business card design for our modern furniture company which supplies furniture and appliances to the property and development market.
Oakridge Interiors has become one of the leading furniture & appliance suppliers to the property market withing London. With over 10 years experience, we have increased our business to supply not only private landlords and managing agents, but also property developers, housing associations and local councils.
We offer not only a complete range of furniture which includes beds, wardrobes, dining sets and sofas, but also a high quality, full delivery and assembly service to help you with all our furnishing needs.

Target Market(s)

Private landlords, estate agents, letting agents, property management companies

Industry/Entity Type

Business

Contact Information for Business Card

Name,
Title,
Address,
Mobile,
Telephone,
Fax, Website, email address

Font styles to use
Sans Serif

Colors
3176b5
0555a3
85abd2
cfdeed

Requirements
Must have
• All the above information for each of our staff, along with our logo

```html
<!DOCTYPE html>
<html lang="en">
<head>
<meta charset="utf-8">
<title>Oakridge Interiors – Business Card</title>
<link href="https://fonts.googleapis.com/css2?family=Roboto+Condensed:wght@400&family=Montserrat:wght@400;500;700&display=swap" rel="stylesheet">
<style>
  :root {
    --backdrop: #2a2a2a;
    --card: #ffffff;
    --ink: #1c1c1c;
    --navy: #1f3a70;
    --blue: #1570b8;
    --rule: #2a3f73;
  }
  html, body {
    margin: 0;
    width: 1189px;
    height: 1200px;
    overflow: hidden;
    background: var(--backdrop);
  }
  .canvas {
    position: relative;
    width: 1189px;
    height: 1200px;
  }
  .card {
    position: absolute;
    left: 171px;
    width: 856px;
    height: 488px;
    background: var(--card);
    border-radius: 20px;
  }
  .card--front { top: 67px; }
  .card--back { top: 627px; }

  .brand {
    position: absolute;
    text-align: center;
    font-family: "Roboto Condensed", "Arial Narrow", sans-serif;
    font-weight: 400;
    color: var(--ink);
  }
  .brand__row {
    display: flex;
    align-items: center;
    justify-content: center;
    gap: 14px;
  }
  .brand__mark {
    width: 30px;
    height: 30px;
    background: var(--navy);
  }
  .brand__name {
    text-transform: uppercase;
    line-height: 1;
    white-space: nowrap;
  }
  .brand__tagline {
    text-transform: uppercase;
    line-height: 1;
    white-space: nowrap;
  }

  .card--front .brand { left: 0; right: 0; top: 190px; }
  .card--front .brand__name { font-size: 40px; }
  .card--front .brand__tagline { font-size: 20px; margin-top: 12px; }

  .card--back .brand { left: 62px; width: 326px; top: 200px; }
  .card--back .brand__mark { width: 24px; height: 24px; }
  .card--back .brand__row { gap: 10px; }
  .card--back .brand__name { font-size: 31px; }
  .card--back .brand__tagline { font-size: 16px; margin-top: 9px; }

  .divider {
    position: absolute;
    left: 419px;
    top: 91px;
    width: 2px;
    height: 304px;
    background: var(--rule);
  }

  .contact {
    position: absolute;
    left: 466px;
    top: 88px;
    font-family: "Montserrat", Arial, sans-serif;
    color: var(--ink);
  }
  .contact__name {
    margin: 0;
    font-size: 29px;
    font-weight: 700;
    color: var(--navy);
    line-height: 1;
    letter-spacing: 0.3px;
  }
  .contact__title {
    margin: 0;
    font-size: 21px;
    line-height: 1;
  }
  .contact__address {
    margin: 33px 0 0;
    font-style: normal;
    font-size: 21px;
    line-height: 31px;
  }
  .contact__list {
    list-style: none;
    margin: 6px 0 0;
    padding: 0;
    font-size: 21px;
  }
  .contact__item {
    display: flex;
    align-items: center;
    gap: 6px;
    height: 29px;
  }
  .contact__icon {
    width: 27px;
    height: 27px;
    flex: none;
  }
  .contact__web {
    margin: 20px 0 0;
    font-size: 21px;
    color: var(--navy);
  }
</style>
</head>
<body>
<main class="canvas">

  <section class="card card--front">
    <div class="brand">
      <div class="brand__row">
        <span class="brand__mark"></span>
        <span class="brand__name">Oakridge Interiors</span>
      </div>
      <div class="brand__tagline">Trade Furniture Solutions</div>
    </div>
  </section>

  <section class="card card--back">
    <div class="brand">
      <div class="brand__row">
        <span class="brand__mark"></span>
        <span class="brand__name">Oakridge Interiors</span>
      </div>
      <div class="brand__tagline">Trade Furniture Solutions</div>
    </div>

    <div class="divider"></div>

    <div class="contact">
      <h1 class="contact__name">DANIEL REYES</h1>
      <p class="contact__title">Maneger</p>
      <address class="contact__address">
        Your Address,2nd Ste<br>
        Brookfield, Texas 1234, USA
      </address>
      <ul class="contact__list">
        <li class="contact__item">
          <svg class="contact__icon" viewBox="0 0 27 27" aria-hidden="true">
            <rect width="27" height="27" rx="3" fill="#1f3a70"/>
            <path d="M9 6c1 0 2 3 2 4s-2 1-1 3 3 4 4 4 1-2 2-1 3 2 3 3-2 3-4 2S9 17 7 12 8 6 9 6z" fill="#fff"/>
          </svg>
          <span>123 456 7890</span>
        </li>
        <li class="contact__item">
          <svg class="contact__icon" viewBox="0 0 27 27" aria-hidden="true">
            <rect width="27" height="27" rx="3" fill="#1f3a70"/>
            <rect x="9" y="5" width="9" height="5" fill="#fff"/>
            <rect x="5" y="10" width="17" height="8" rx="1" fill="#fff"/>
            <rect x="9" y="15" width="9" height="7" fill="#fff" stroke="#1f3a70" stroke-width="1"/>
          </svg>
          <span>123 456 7890</span>
        </li>
        <li class="contact__item">
          <svg class="contact__icon" viewBox="0 0 27 27" aria-hidden="true">
            <rect width="27" height="27" rx="3" fill="#1f3a70"/>
            <rect x="9" y="4" width="9" height="19" rx="1.5" fill="#fff"/>
            <rect x="10.5" y="6.5" width="6" height="6" fill="#1f3a70"/>
          </svg>
          <span>123 456 7890</span>
        </li>
        <li class="contact__item">
          <svg class="contact__icon" viewBox="0 0 27 27" aria-hidden="true">
            <rect width="27" height="27" rx="3" fill="#1f3a70"/>
            <rect x="5" y="8" width="17" height="12" fill="#fff"/>
            <path d="M5 8l8.5 7L22 8M5 20l6-6M22 20l-6-6" fill="none" stroke="#1f3a70" stroke-width="1.3"/>
          </svg>
          <span>your@yourcompany.com</span>
        </li>
      </ul>
      <p class="contact__web">www.yourcompany.com</p>
    </div>
  </section>

</main>
</body>
</html>
```